Business Card Design (NEW FILES)

ATTENTION: New vector files are available. Please update your design to reflect/use the new (better resolution) logo images.

Seeking a unique and professional business card design for a commercial drone photography/videography business. The layout should feature
the logo (attached) and include the following information:
Owen Tarrick
614-502-7738
www.skylarkreelworks.example
NRD Certified Remote Pilot

Owen Tarrick

```html
<!DOCTYPE html>
<html lang="en">
<head>
<meta charset="utf-8">
<title>Skylark Reelworks – Business Card</title>
<link href="https://fonts.googleapis.com/css2?family=Open+Sans:ital,wght@0,400;0,600;0,700;1,600&family=Montserrat:wght@500;800&display=swap" rel="stylesheet">
<style>
  :root {
    --stage: #222222;
    --paper: #f4f4f4;
    --orange: #e3874f;
    --orange-deep: #d9733a;
    --orange-light: #eea36f;
    --navy: #161a48;
    --ghost: #dcdce0;
  }
  * { box-sizing: border-box; margin: 0; padding: 0; }
  html, body { width: 1200px; height: 780px; overflow: hidden; }
  body {
    background: var(--stage);
    font-family: "Open Sans", Arial, sans-serif;
    position: relative;
  }
  .card {
    position: absolute;
    top: 242px;
    width: 520px;
    height: 297px;
    border-radius: 3px;
    overflow: hidden;
    box-shadow: 0 14px 30px rgba(0,0,0,.45);
  }
  .card--front { left: 60px; background: var(--paper); }
  .card--back { left: 620px; background: var(--orange); }

  /* front */
  .wordmark {
    position: absolute;
    left: 150px;
    top: 28px;
    display: flex;
    align-items: center;
    gap: 10px;
  }
  .wordmark__dot {
    width: 16px; height: 16px; border-radius: 50%;
    background: var(--orange);
  }
  .wordmark__name {
    font-family: "Open Sans", Arial, sans-serif;
    font-weight: 600;
    font-size: 26px;
    letter-spacing: 1px;
    color: var(--navy);
    text-transform: uppercase;
  }
  .tagline {
    position: absolute;
    left: 176px;
    top: 66px;
    font-size: 9px;
    font-weight: 700;
    letter-spacing: 1.5px;
    color: var(--orange);
    text-transform: uppercase;
  }
  .credentials {
    position: absolute;
    left: 38px;
    top: 104px;
    color: var(--navy);
    font-weight: 600;
    font-size: 13px;
    line-height: 20px;
  }
  .contact { list-style: none; margin-top: 4px; }
  .contact li { display: flex; align-items: center; gap: 8px; }
  .contact svg { width: 12px; height: 12px; flex: none; }
  .swoosh { position: absolute; left: 0; bottom: 0; width: 520px; height: 297px; }
  .decor-faint {
    position: absolute;
    left: 290px; top: 120px;
    width: 200px; height: 90px;
    border-radius: 45px;
    background: radial-gradient(ellipse at center, rgba(210,210,216,.55), rgba(244,244,244,0) 70%);
  }
  .holder {
    position: absolute;
    right: 44px;
    top: 206px;
    text-align: right;
    font-family: "Montserrat", Arial, sans-serif;
  }
  .holder__name { font-size: 26px; font-weight: 800; color: var(--navy); line-height: 1; }
  .holder__name .first { color: var(--orange); }
  .holder__role { font-size: 13px; font-weight: 500; color: var(--navy); margin-top: 6px; }
  .accent-bar {
    position: absolute;
    right: 0; top: 206px;
    width: 34px; height: 52px;
    background: var(--orange);
  }

  /* back */
  .back-decor {
    position: absolute;
    left: 150px; top: 20px;
    width: 350px; height: 250px;
    border-radius: 50%;
    background: radial-gradient(ellipse at 60% 50%, rgba(238,163,111,.8), rgba(227,135,79,0) 70%);
  }
  .back-wordmark {
    position: absolute;
    left: 40px; top: 120px;
    display: flex; align-items: center; gap: 10px;
  }
  .back-wordmark .wordmark__name { color: var(--orange-deep); font-size: 24px; }
  .back-wordmark .wordmark__dot { background: var(--orange-light); width: 22px; height: 22px; }
</style>
</head>
<body>

<section class="card card--front" aria-label="Business card front">
  <div class="wordmark">
    <span class="wordmark__dot"></span>
    <span class="wordmark__name">Skylark Reelworks</span>
  </div>
  <p class="tagline">Captivating Aerial Imagery</p>

  <div class="credentials">
    <p>NRD Certified Remote Pilot</p>
    <p>Fully Insured</p>
    <ul class="contact">
      <li>
        <svg viewBox="0 0 12 12" aria-hidden="true"><path d="M3 1 L5 3.5 L4 5 Q5 7 7 8 L8.5 7 L11 9 L9.5 11 Q4 10.5 1 3 Z" fill="var(--orange)"/></svg>
        614-502-7738
      </li>
      <li>
        <svg viewBox="0 0 12 12" aria-hidden="true"><circle cx="6" cy="6" r="5" fill="none" stroke="var(--orange)" stroke-width="1.6"/><path d="M1 6 H11 M6 1 Q3 6 6 11 M6 1 Q9 6 6 11" fill="none" stroke="var(--orange)" stroke-width="1"/></svg>
        www.skylarkreelworks.example
      </li>
    </ul>
  </div>

  <div class="decor-faint" role="img" aria-label="Faint drone illustration in the background"></div>

  <svg class="swoosh" viewBox="0 0 520 297" aria-hidden="true">
    <path d="M0 200 Q180 225 300 297 L0 297 Z" fill="var(--orange)"/>
    <path d="M0 220 Q170 240 270 297 L0 297 Z" fill="var(--paper)"/>
    <path d="M0 228 Q160 246 255 297 L0 297 Z" fill="var(--navy)"/>
  </svg>

  <div class="holder">
    <p class="holder__name"><span class="first">Owen</span> Tarrick</p>
    <p class="holder__role">Owner</p>
  </div>
  <div class="accent-bar"></div>
</section>

<section class="card card--back" aria-label="Business card back">
  <div class="back-decor" role="img" aria-label="Embossed drone illustration"></div>
  <div class="back-wordmark">
    <span class="wordmark__dot"></span>
    <span class="wordmark__name">Skylark Reelworks</span>
  </div>
</section>

</body>
</html>
```